lofty birch website

We need a new website for our new business division. We are a sustainable design firm specializing in servicing the needs if architects and developers. We have a staff consisting of architects, engineers, and former contractors and we understand green must make sense.

Bottomline - the only sustainable and lofty birch solutions are those thatbare good for the environment and good for our clients bottom line.

Our company is lofty birch and we will send you a copy of our logo you will see our tagline. Is simple. sustainable. solutions. The play with the periods is that we believe their are simple sustainable solutions and we want to use the words together and possible let each stand alone to accentuate their individual meaning in regards to benefit to our clients.

We want a cool splash page with nich graphics and pictures then later pages to feature projects and design ideas.

Target Market(s)

Our target customers are architects, developers, and contractors who would need assistance with the design process for a VARO project or assisatnce with a building owner who wants to make tehir facilty more environmentally friendly and save energy costs at the same tiem.

Industry/Entity Type

Environment

Requirements
Must have
• Needs a construction look with an environmentally friendly surrounding that is pleasing to look at. Must appeal to the client not only as environmentally friendly but also a wise investment.
Nice to have
• Opportunity for a connection to Social networking including a blog.
Should not have
• A totally environmental building feel at whatever cost. We want to emphasize that it is possible to build environmental friendly and save you money over the life of your building

```html
<!DOCTYPE html>
<html lang="en">
<head>
<meta charset="utf-8">
<title>lofty birch — simple. sustainable. solutions.</title>
<link href="https://fonts.googleapis.com/css2?family=Arimo:wght@400;700&display=swap" rel="stylesheet">
<style>
  :root {
    --black: #000000;
    --green: #3fd11a;
    --green-bright: #33ff00;
    --green-deep: #2f9a12;
    --sky: #3f86d0;
    --grass: #58a81f;
    --white: #ffffff;
    --ink: #111111;
    --logo-grey: #5b5b5b;
    --panel: rgba(235, 235, 235, 0.72);
  }
  * { margin: 0; padding: 0; box-sizing: border-box; }
  html, body { width: 1200px; height: 748px; overflow: hidden; }
  body {
    font-family: "Arimo", Arial, sans-serif;
    position: relative;
    background: linear-gradient(to bottom, var(--sky) 0%, #8cc0e8 30%, #2d7a18 36%, var(--grass) 60%, #9fd34a 100%);
  }
  .site { position: absolute; left: 45px; top: 0; width: 1114px; height: 748px; background: var(--black); }

  .topbar { position: absolute; left: 0; top: 0; width: 1114px; height: 40px; background: var(--black); }
  .nav { list-style: none; position: absolute; left: 0; top: 0; height: 40px; }
  .nav li { position: absolute; top: 0; height: 40px; line-height: 38px; color: var(--white); font-weight: 700; font-size: 15px; }
  .nav li.active { background: linear-gradient(to bottom, #47d91e, #2aa40c); text-align: center; }
  .callus { position: absolute; right: 25px; top: 7px; color: var(--green-bright); font-size: 20px; }

  .hero {
    position: absolute; left: 0; top: 40px; width: 1114px; height: 520px;
    background: linear-gradient(to bottom, #d9d9d9 0%, #b8b8b8 25%, #6a6a6a 55%, #2a2a2a 100%);
  }
  .hero-city { position: absolute; inset: 0; }
  .brand { position: absolute; left: 22px; top: 12px; display: flex; align-items: center; gap: 12px; }
  .brand-mark { width: 40px; height: 40px; background: var(--green-deep); }
  .brand-name { font-size: 44px; color: var(--logo-grey); font-weight: 400; line-height: 1; }
  .brand-tagline { position: absolute; left: 74px; top: 66px; font-size: 18px; color: var(--logo-grey); }

  .feature { position: absolute; left: 117px; top: 132px; width: 881px; height: 283px; background: var(--panel); }
  .feature-photo {
    position: absolute; right: 0; top: 0; width: 331px; height: 283px;
    background:
      linear-gradient(to right, rgba(225,225,225,0.95) 0%, rgba(225,225,225,0.55) 14%, rgba(225,225,225,0) 30%),
      radial-gradient(ellipse at 60% 45%, #c7a38a 0%, #9bc45a 45%, #6fc02a 100%);
  }
  .feature-title { position: absolute; z-index: 2; left: 21px; top: 36px; font-size: 26px; font-weight: 700; line-height: 38px; color: var(--ink); }
  .feature-copy { position: absolute; z-index: 2; left: 21px; top: 155px; width: 548px; font-size: 12.5px; line-height: 17px; color: var(--ink); }
  .feature-copy p + p { margin-top: 17px; }
  .slider-dots { position: absolute; z-index: 2; right: 10px; bottom: 8px; display: flex; gap: 4px; }
  .slider-dots span { width: 19px; height: 19px; background: #e6e6e6; border: 1px solid #bbbbbb; }
  .slider-dots span.on { background: var(--green-bright); }

  .wave { position: absolute; left: 0; top: 460px; width: 1114px; height: 230px; }

  .intro { position: absolute; left: 31px; top: 572px; font-size: 12.6px; line-height: 17.2px; color: var(--green-bright); }

  .gallery-photo { position: absolute; top: 486px; height: 189px; }
  .gallery-photo.living { left: 444px; width: 340px; background: linear-gradient(135deg, #c9c4bb 0%, #8d8a84 50%, #3b3a38 100%); }
  .gallery-photo.loft { left: 797px; width: 317px; background: linear-gradient(135deg, #e6e2da 0%, #a69b8a 55%, #5a4a3a 100%); }

  .band { position: absolute; left: 0; top: 687px; width: 1114px; height: 8px; background: linear-gradient(to right, var(--green-deep), var(--green), var(--green-deep)); }
  .footer { position: absolute; left: 0; top: 695px; width: 1114px; height: 53px; background: var(--black); }
  .copyright { position: absolute; left: 15px; top: 18px; font-size: 13px; color: var(--white); }
  .social { position: absolute; right: 18px; top: 10px; display: flex; gap: 10px; }
  .social span { width: 32px; height: 32px; border-radius: 5px; }
  .social .s1 { background: #4fb7e6; }
  .social .s2 { background: #2f66b0; }
  .social .s3 { background: #f39a1d; }
</style>
</head>
<body>
<div class="site">
  <header class="topbar">
    <ul class="nav">
      <li style="left:34px">HOME</li>
      <li class="active" style="left:108px;width:93px">BLOG</li>
      <li style="left:226px">SAMRT</li>
      <li style="left:329px">GREEN</li>
      <li style="left:435px">PROJECTS</li>
    </ul>
    <div class="callus">Call us 555.014.2290</div>
  </header>

  <section class="hero">
    <div class="hero-city" role="img" aria-label="Black and white skyline of a dense city"></div>
    <div class="brand">
      <span class="brand-mark"></span>
      <span class="brand-name">lofty birch</span>
    </div>
    <div class="brand-tagline">simple. sustainable. solutions.</div>

    <div class="feature">
      <div class="feature-photo" role="img" aria-label="Portrait of a smiling client against green foliage"></div>
      <h1 class="feature-title">SIMPLE<br>SUSTAINABLE<br>SOLUTIONS</h1>
      <div class="feature-copy">
        <p>Lorem Ipsum dolor sit ipsum Lorem Ipsum dolor sit ipsum Lorem Ipsum dolor sit ipsum Lorem Ipsum dolor sit ipsum Lorem Ipsum dolor sit ipsum</p>
        <p>Lorem Ipsum dolor sit ipsum Lorem Ipsum dolor sit ipsum Lorem Ipsum dolor sit ipsum Lorem Ipsum dolor sit ipsum Lorem Ipsum dolor sit ipsum</p>
      </div>
      <div class="slider-dots"><span></span><span class="on"></span><span></span><span></span></div>
    </div>
  </section>

  <svg class="wave" viewBox="0 0 1114 230" aria-hidden="true">
    <path d="M0,51 C120,110 260,100 420,75 C640,40 900,15 1114,8 L1114,230 L0,230 Z" fill="#000"/>
    <path d="M0,51 C120,110 260,100 420,75 C640,40 900,15 1114,8" fill="none" stroke="#33ff00" stroke-width="4"/>
  </svg>

  <div class="intro">
    Lorem Ipsum dolor sit ipsum Lorem Ipsum dolor sit ipsum<br>
    Lorem Ipsum dolor sit ipsum Lorem Ipsum dolor sit ipsum<br>
    Lorem Ipsum dolor sit ipsum<br>
    Lorem Ipsum dolor sit ipsum Lorem Ipsum dolor sit ipsum<br>
    Lorem Ipsum dolor sit ipsum Lorem Ipsum dolor sit ipsum<br>
    Lorem Ipsum dolor sit ipsum
  </div>

  <div class="gallery-photo living" role="img" aria-label="Bright modern living room with white sofas"></div>
  <div class="gallery-photo loft" role="img" aria-label="Loft interior with tall windows and lounge seating"></div>

  <div class="band"></div>
  <footer class="footer">
    <div class="copyright">Copyright@ 2011&nbsp; loftybirch</div>
    <div class="social"><span class="s1"></span><span class="s2"></span><span class="s3"></span></div>
  </footer>
</div>
</body>
</html>
```